Healthcare and Professional IT Services Company need a redesigned business card

We are a IT Services company that targets small medical practices and professional business such as Attorneys, Accounts, Architects etc. We want to communicate a professional yet friendly image using recent logo redesign here on ArtHarbor. Like to see the colors blue and orange in the design. Must use the Tall Pine Computing as displayed in the new logo - then also want to incorporate the fish logo as well.

Target Market(s)

Small medical and professional services

Industry/Entity Type

It Company

Contact Information for Business Card

The usual stuff, place for name address phone website. Also maybe our tagline which is "Rooted in technology"

Requirements
Must have
• My new logo and the fish somewhere on the card

```html
<!DOCTYPE html>
<html lang="en">
<head>
<meta charset="UTF-8">
<title>Tall Pine Computing – Business Card</title>
<link rel="stylesheet" href="https://fonts.googleapis.com/css2?family=Source+Sans+3:wght@400;600&display=swap">
<style>
  :root {
    --brand-blue: #1a8fd6;
    --brand-orange: #f39221;
    --ink: #4a4a4a;
    --card: #fbfbfb;
    --backdrop: #3b3b3b;
    --mascot-light: #dceef9;
    --mascot-mid: #b8dcf2;
  }
  * { box-sizing: border-box; margin: 0; padding: 0; }
  html, body {
    width: 1200px;
    height: 750px;
    overflow: hidden;
    background: var(--backdrop);
    font-family: "Source Sans 3", "Helvetica Neue", Arial, sans-serif;
  }
  .stage {
    position: relative;
    width: 1200px;
    height: 750px;
  }
  .card {
    position: absolute;
    top: 227px;
    width: 520px;
    height: 296px;
    background: var(--card);
    overflow: hidden;
  }
  .card--front { left: 60px; }
  .card--back { left: 620px; }

  /* Front */
  .mascot-area {
    position: absolute;
    left: 0;
    top: 0;
    width: 280px;
    height: 296px;
    background: radial-gradient(ellipse at 55% 45%, var(--mascot-mid), var(--mascot-light) 70%, var(--card));
  }
  .edge-tab {
    position: absolute;
    right: 0;
    top: 104px;
    width: 10px;
    height: 40px;
    background: var(--brand-blue);
    border-radius: 20px 0 0 20px;
  }
  .details {
    position: absolute;
    right: 31px;
    top: 0;
    text-align: right;
  }
  .brand-name {
    position: absolute;
    right: 0;
    white-space: nowrap;
    font-weight: 600;
    color: var(--brand-blue);
  }
  .card--front .brand-name {
    top: 44px;
    font-size: 22px;
  }
  .person-name {
    position: absolute;
    right: 0;
    top: 104px;
    white-space: nowrap;
    font-size: 19px;
    font-weight: 600;
    color: var(--brand-blue);
  }
  .person-title {
    position: absolute;
    right: 0;
    top: 128px;
    white-space: nowrap;
    font-size: 14px;
    color: var(--brand-orange);
  }
  .address {
    position: absolute;
    right: 2px;
    top: 166px;
    white-space: nowrap;
    font-size: 13px;
    line-height: 16px;
    color: var(--ink);
    font-style: normal;
  }
  .contacts {
    position: absolute;
    right: 0;
    top: 219px;
    list-style: none;
  }
  .contacts li {
    display: flex;
    justify-content: flex-end;
    align-items: center;
    gap: 8px;
    height: 20px;
    white-space: nowrap;
    font-size: 13px;
    color: var(--ink);
  }
  .contacts svg { width: 14px; height: 14px; flex: none; }

  /* Back */
  .mascot-badge {
    position: absolute;
    left: 196px;
    top: 72px;
    width: 132px;
    height: 90px;
    border-radius: 45px;
    background: radial-gradient(ellipse at 55% 45%, var(--mascot-mid), var(--mascot-light) 75%, var(--card));
  }
  .card--back .brand-name {
    position: absolute;
    left: 0;
    right: 0;
    top: 174px;
    text-align: center;
    font-size: 26px;
  }
  .tagline {
    position: absolute;
    left: 0;
    right: 0;
    top: 248px;
    text-align: center;
    font-size: 15px;
    color: var(--brand-orange);
  }
</style>
</head>
<body>
<main class="stage">
  <section class="card card--front" aria-label="Business card front">
    <div class="mascot-area" role="img" aria-label="Large cartoon mascot illustration in blue outline"></div>
    <div class="edge-tab"></div>
    <div class="details">
      <p class="brand-name">Tall Pine Computing</p>
      <p class="person-name">Dana Reyes</p>
      <p class="person-title">CEO/Founder</p>
      <address class="address">4120 Cedar Hollow Road<br>Bellingham, Washington 98226</address>
      <ul class="contacts">
        <li>360 555 0147
          <svg viewBox="0 0 16 16" aria-hidden="true"><path fill="var(--brand-blue)" d="M4.2 1.5l2 2.6-1.2 1.5c.8 1.9 2.4 3.5 4.3 4.3l1.5-1.2 2.6 2-1.3 2.4C7.3 13 3 8.7 1.9 2.8z"/></svg>
        </li>
        <li>dana@tallpinecomputing.com
          <svg viewBox="0 0 16 16" aria-hidden="true"><rect x="1" y="3.5" width="14" height="9.5" fill="var(--brand-blue)"/><path d="M1.5 4l6.5 5 6.5-5" fill="none" stroke="#fff" stroke-width="1.2"/></svg>
        </li>
        <li>www.tallpinecomputing.com
          <svg viewBox="0 0 16 16" aria-hidden="true"><circle cx="8" cy="8" r="7" fill="var(--brand-blue)"/><path d="M1 8h14M8 1c-3 3.5-3 10.5 0 14M8 1c3 3.5 3 10.5 0 14" fill="none" stroke="#fff" stroke-width="1"/></svg>
        </li>
      </ul>
    </div>
  </section>

  <section class="card card--back" aria-label="Business card back">
    <div class="mascot-badge" role="img" aria-label="Small cartoon mascot illustration"></div>
    <p class="brand-name">Tall Pine Computing</p>
    <p class="tagline">Rooted in technology</p>
  </section>
</main>
</body>
</html>
```